Business Cards for a law firm

Business cards for our law firm. Use our silhoette logo and OAK PARTNERS - check our website (www.oakpartners.example)

Contact Information for Business Card

our silhouette logo, OAK PARTNERS, 800-555-0147, Dorian Pemberton, dorian@oakpartners.example

Requirements
Must have
• our silhouette logo, OAK PARTNERS, 800-555-0147, Dorian Pemberton, dorian@oakpartners.example

```html
<!DOCTYPE html>
<html lang="en">
<head>
<meta charset="utf-8">
<title>Oak Partners – Business Cards</title>
<link rel="stylesheet" href="https://fonts.googleapis.com/css2?family=Lexend+Zetta:wght@300&family=Montserrat:wght@400;700&display=swap">
<style>
  :root {
    --navy: #243670;
    --white: #ffffff;
    --ink: #1d1d24;
    --backdrop: #2b2b2d;
  }
  * { box-sizing: border-box; margin: 0; padding: 0; }
  html, body {
    width: 1200px; height: 900px; overflow: hidden;
    background: var(--backdrop);
  }
  .canvas {
    position: relative; width: 1200px; height: 900px;
  }
  .card {
    position: absolute; left: 250px; width: 700px; height: 400px;
    border-radius: 28px; overflow: hidden;
  }
  .card--front { top: 40px; background: var(--white); }
  .card--back { top: 470px; background: var(--navy); }

  .brand {
    position: absolute; display: flex; align-items: center; gap: 18px;
    font-family: "Lexend Zetta", sans-serif; font-weight: 300;
    font-size: 34px; letter-spacing: 1px; white-space: nowrap;
  }
  .brand__mark { width: 40px; height: 40px; display: block; }
  .card--front .brand { left: 56px; top: 96px; color: var(--navy); }
  .card--front .brand__mark { background: var(--navy); }
  .card--back .brand { left: 90px; top: 176px; color: var(--white); }
  .card--back .brand__mark { background: var(--white); }

  .holder { position: absolute; left: 56px; top: 212px; }
  .holder__name {
    font-family: "Montserrat", sans-serif; font-weight: 700;
    font-size: 28px; color: var(--navy);
  }
  .holder__title {
    font-family: "Montserrat", sans-serif; font-weight: 400;
    font-size: 15px; color: var(--ink); margin-top: 2px;
  }
  .divider {
    position: absolute; left: 56px; right: 50px; top: 285px;
    height: 2px; background: var(--navy);
  }
  .contacts {
    position: absolute; left: 56px; top: 302px; list-style: none;
    font-family: "Montserrat", sans-serif; font-size: 15px; color: var(--ink);
  }
  .contacts li { display: flex; align-items: center; gap: 12px; height: 25px; }
  .contacts svg { width: 14px; height: 14px; fill: var(--navy); flex: none; }
</style>
</head>
<body>
<main class="canvas">
  <section class="card card--front">
    <div class="brand"><span class="brand__mark"></span>OAK PARTNERS</div>
    <div class="holder">
      <p class="holder__name">Dorian Pemberton</p>
      <p class="holder__title">Attorney at Law</p>
    </div>
    <div class="divider"></div>
    <ul class="contacts">
      <li>
        <svg viewBox="0 0 16 16" aria-hidden="true"><path d="M3 1h3l1.5 4-2 1.3a9 9 0 0 0 4.2 4.2L11 8.5l4 1.5v3a2 2 0 0 1-2 2A12 12 0 0 1 1 3a2 2 0 0 1 2-2z"/></svg>
        800-555-0147
      </li>
      <li>
        <svg viewBox="0 0 16 16" aria-hidden="true"><path d="M1 3h14v1.2L8 9 1 4.2z"/><path d="M1 6l7 4.8L15 6v7H1z"/></svg>
        dorian@oakpartners.example
      </li>
      <li>
        <svg viewBox="0 0 16 16" aria-hidden="true"><path d="M8 1a7 7 0 1 0 0 14A7 7 0 0 0 8 1zm0 1.5c.9 0 1.9 1.7 2.2 4.5H5.8C6.1 4.2 7.1 2.5 8 2.5zM2.6 7h1.8c.1-1.6.4-3 1-4A5.5 5.5 0 0 0 2.6 7zm8.9 0h1.9a5.5 5.5 0 0 0-2.9-4c.6 1 .9 2.4 1 4zM2.6 9a5.5 5.5 0 0 0 2.8 4c-.6-1-.9-2.4-1-4zm3.2 0c.3 2.8 1.3 4.5 2.2 4.5s1.9-1.7 2.2-4.5zm5.7 0c-.1 1.6-.4 3-1 4a5.5 5.5 0 0 0 2.9-4z"/></svg>
        www.oakpartners.example
      </li>
    </ul>
  </section>

  <section class="card card--back">
    <div class="brand"><span class="brand__mark"></span>OAK PARTNERS</div>
  </section>
</main>
</body>
</html>
```